CODED website - Breakfree418

I am a successful entrepreneur - have recently sold my business and am semi-retired. I want to give something back, as well as provide a blog for articles and my journeys.

I will also be using this to provide free business and entrepreneurial advice.

I am creating a NOT FOR PROFIT business called Breakfree418.com.au which will provide the following;

1. Blog and articles; my travels, Small to Medium business advice and articles

2. My Bucket List - the 100 things I aim to achieve

3. Free business / start up advice - a section on the website which provides case studies on people / businesses which ask me for advice. We will then chronicle their story and what advice we have given for them to succeed.

My inspiration is the Martin Oxendale idea and website;

http://martinoxendale.example/about-martin/

Obviously I do NOT want a copy of this site, but use this for inspiration.

Furthermore, I would be interested in ongoing collaboration with the successful designer - I will be providing advice and consultancy to start ups, all of which will need web design etc, so there is ongoing referral streams for the successful designer.

I need this to be CODED and then uplifted to the website, so please DO NOT bid on this unless you can provide a coded site and facilitate the upload to BrightHosting.

The NECESSARY tabs / pages

Main landing page - a short introduction into the ethos of Breakfree418

Writing - this will be the blog articles

About

Our Bucket List - a section where we can add our 100 buket list items. Hyperlinked to open a new page which has details on each bucket list item (ie #1 Make Breakfree418 - hyperlink to a new page which then has info on the bucklist item and what we have done)

Breakfree418 - this will be the section where we discuss people / businesses that we are helping. We will have an opening intro section + a link to the contact us page so they can ask us for the free advice. This will be the section where we have case studies into businesses / people that we have helped.

Hey everyone!

I'm really keen to get this website launched and looking amazing - if you have any questions, or would like to discuss anything at all, please email me at

dane@pollwick.example.com.au

As I mentioned in the brief, I am doing this site to give back; I will not be earning a cent, and I will not be trying to earn any funds. I'm doing it simply to help other start ups or entrepreneurs, so I really want this site to look amazing.

I hope someone reads this and is inspired, and wants to be involved in this social enterprise with me.

Really excited to hear from you all and see your designs!

Industry/Entity Type

Business

Requirements
Must have
• MUST BE CODED and uplifted to the BrightHosting registered domain - www.breakfree418.com.au - happy to discuss additional costings for this with successful designer.

Separate pages for each section (as outlined in the brief above)

Blog section to look similar to http://martinoxendale.example/3x5/

Comprehensive website - not a simple wordpress template theme with some minor modifications. I will immediately reject any simple template design. I am looking for a slick, fully functioning website design.

PLEASE BE AWARE that I am looking for ongoing collaboration with the www.breakfree418.com.au.

I am trying this website as I want to find a young, energetic, vibrant, dynamic designer - this is your opportunity to be a part of something big, as this website will be huge!

Please do not submit a design if you are not motivated and ready for something big.

```html
<!DOCTYPE html>
<html lang="en">
<head>
<meta charset="utf-8">
<title>Breakfree418</title>
<link href="https://fonts.googleapis.com/css2?family=Ubuntu:ital,wght@0,400;0,500;0,700;1,700&family=Open+Sans:wght@400;700;800&display=swap" rel="stylesheet">
<style>
:root{
  --olive:#6d6b2c;
  --olive-dark:#57561f;
  --paper:#ebe3c0;
  --card:#fbfaf5;
  --dark:#2f2f2f;
  --ink:#3b3a33;
  --muted:#5a584c;
  --link:#3a9bd1;
  --accent:#6b6a22;
}
*{margin:0;padding:0;box-sizing:border-box}
html,body{width:781px;height:1200px;overflow:hidden}
body{position:relative;background:linear-gradient(90deg,var(--olive-dark),var(--olive) 8%,var(--olive) 92%,var(--olive-dark));font-family:"Ubuntu",sans-serif;color:var(--ink)}
.page{position:absolute;left:76px;top:0;width:628px;height:1153px;background:var(--paper)}
.abs{position:absolute}
.logo{left:96px;top:40px;width:150px;font:700 21px/1 "Ubuntu",sans-serif;color:#222;white-space:nowrap}
.nav{left:258px;top:38px;width:428px;height:37px;border-top:3px double #bdb48c;border-bottom:3px double #bdb48c;display:flex;justify-content:space-around;align-items:center;font-size:12px;color:#333}
.nav a{color:#333;text-decoration:none;position:relative}
.nav a.on::after{content:"";position:absolute;left:50%;bottom:-8px;margin-left:-3px;border:3px solid transparent;border-top-width:0;border-bottom:4px solid #333}
.slider{left:94px;top:88px;width:592px;height:210px;background:#fff;box-shadow:0 4px 6px rgba(0,0,0,.25);padding:8px}
.slide{width:576px;height:194px;position:relative;background:linear-gradient(180deg,#d9d3c6 0%,#b7a38a 45%,#9b6b45 75%,#7a4b2e 100%)}
.slide .rock{position:absolute;right:0;top:60px;width:270px;height:134px;background:linear-gradient(160deg,#b8622e,#8a4a24)}
.caption{position:absolute;font-family:"Open Sans",sans-serif;font-weight:800;font-style:italic;line-height:1}
.c1{left:82px;top:52px;font-size:30px;color:#fff}
.c2{left:46px;top:84px;font-size:36px;color:var(--accent)}
.c3{left:114px;top:118px;font-size:20px;color:#222}
.c4{left:48px;top:140px;font-size:13px;color:#fff}
.dots{position:absolute;right:16px;bottom:14px;display:flex;gap:5px}
.dots i{width:7px;height:7px;border-radius:50%;background:#fff}
h2.sec{position:absolute;left:94px;font:400 23px "Ubuntu",sans-serif;color:#2a2a2a}
.copy{left:94px;width:385px;font:6.6px/9px "Open Sans",sans-serif;color:var(--muted);text-align:justify}
.btn{background:var(--dark);color:#fff;font:9px "Open Sans",sans-serif;display:flex;align-items:center;justify-content:center;box-shadow:1px 1px 2px rgba(0,0,0,.4)}
.bar{left:94px;width:385px;height:35px;background:var(--dark);color:#fff;display:flex;justify-content:space-between;align-items:center;padding:0 14px;font-size:15px;box-shadow:0 2px 3px rgba(0,0,0,.3)}
.bar small{font:8px "Open Sans",sans-serif}
.card{width:124px;height:179px;background:var(--card);border:1px solid #ddd6b8;padding:8px}
.card .ph{height:72px;border:4px solid #fff;box-shadow:0 1px 3px rgba(0,0,0,.35);margin-bottom:17px}
.card h4{font:500 8.6px "Ubuntu",sans-serif;color:#555;margin-bottom:8px}
.card p{font:6.6px/9px "Open Sans",sans-serif;color:#666;text-align:justify;height:40px}
.card a{font:6.6px "Open Sans",sans-serif;color:#555;text-decoration:underline;display:block;margin-top:4px}
.side{left:493px;width:193px;background:var(--card);border:1px solid #ddd6b8}
.shead{left:493px;width:193px;height:34px;background:var(--dark);color:#fff;font-size:13.5px;padding:9px 12px;box-shadow:0 2px 3px rgba(0,0,0,.3);letter-spacing:.3px}
.bucket{display:flex;gap:8px;padding:0 6px 8px 13px;margin-bottom:7px;border-bottom:1px dotted #ccc}
.bucket .th{flex:0 0 57px;height:42px;border:3px solid #fff;box-shadow:0 1px 3px rgba(0,0,0,.35)}
.bucket b{display:block;font:400 9px Arial,sans-serif;color:var(--link);margin-bottom:2px}
.bucket p{font:7px/11.5px Arial,sans-serif;color:#555}
.news{padding:0 12px 0 14px;font:7px/11.5px Arial,sans-serif;color:#555;margin-bottom:11px}
.news a{color:var(--link);text-decoration:none;display:block}
.news em{display:block}
.ethos{left:94px;top:1002px;width:385px;height:140px;background:var(--card);border:1px solid #ddd6b8}
.video{position:absolute;left:16px;top:18px;width:160px;height:104px;border:3px solid #fff;box-shadow:0 1px 3px rgba(0,0,0,.35);background:linear-gradient(180deg,#1c74b4,#0f5690 70%,#123)}
.ethos h3{position:absolute;left:196px;top:14px;font:400 11.5px "Ubuntu",sans-serif;color:#555}
.ethos p{position:absolute;left:196px;top:35px;width:176px;font:6.6px/8.8px "Open Sans",sans-serif;color:#666;text-align:justify}
.input{left:506px;top:1049px;width:166px;height:25px;background:#d6d6d6;border:1px solid #c2c2c2;font:9px "Ubuntu",sans-serif;color:#666;padding:7px 8px;letter-spacing:.4px}
.social{left:510px;top:1102px;font:7.5px "Open Sans",sans-serif;color:#333}
.icons{left:510px;top:1114px;display:flex;gap:2px}
.icons i{width:16px;height:16px;border-radius:50%;background:#222}
.footer{position:absolute;left:0;top:1153px;width:781px;height:47px;background:#2b2b2b;color:#eee;font:8.5px "Open Sans",sans-serif}
.footer span{position:absolute;top:18px}
</style>
</head>
<body>
<div class="page"></div>

<div class="abs logo">Breakfree418</div>
<nav class="abs nav"><a class="on">Home</a><a>About</a><a>Places</a><a>Articles</a><a>Advices</a><a>Blog</a><a>Contact Us</a></nav>

<div class="abs slider">
  <div class="slide" role="img" aria-label="Traveller sitting on a canyon cliff edge at sunrise">
    <div class="rock"></div>
    <div class="caption c1">LORE</div>
    <div class="caption c2">COMMOD</div>
    <div class="caption c3">AE MASSAA</div>
    <div class="caption c4">LOREM IPSUM DOLOR SIT AM</div>
    <div class="dots"><i></i><i></i><i></i><i></i></div>
  </div>
</div>

<h2 class="sec" style="top:312px">Welcome to Our Site</h2>
<p class="abs copy" style="top:349px">Lorem ipsum dolor sit amet, consectetuer adipiscing elit. Aenean commodo ligula eget dolor. Aenean massa. Cum sociis natoque penatibus et magnis dis parturient montes, nascetur ridiculus mus. Donec quam felis, ultricies nec, pellentesque eu, pretium quis, sem. Nulla consequat massa quis enim. Donec pede justo, fringilla vel, aliquet nec, vulputate eget, arcu. In enim justo, rhoncus ut, imperdiet a, venenatis vitae,Lorem ipsum dolor sit amet, consectetuer adipiscing elit. Nulla consequat massa quis enim.</p>
<p class="abs copy" style="top:403px">Donec pede justo. Lorem ipsum dolor sit amet, consectetuer adipiscing elit. Aenean commodo ligula eget dolor. Aenean massa. Cum sociis natoque penatibus et magnis dis parturient montes, nascetur ridiculus mus.</p>
<div class="abs btn" style="left:94px;top:434px;width:72px;height:24px">View More</div>

<h2 class="sec" style="top:470px">Latest Articles</h2>
<div class="abs bar" style="top:506px">Travel Articles<small>View More...</small></div>
<div class="abs card" style="left:94px;top:548px"><div class="ph" role="img" aria-label="Happy family on a trip" style="background:linear-gradient(180deg,#9fc3e0,#d9b89a)"></div><h4>Lorem ipsum dolor sit</h4><p>Aenean commodo ligula eget dolor. Aenean massa. Cum sociis natoque penatibus et magnis dis parturient adipiscing elit.</p><a>View More...</a></div>
<div class="abs card" style="left:225px;top:548px"><div class="ph" role="img" aria-label="Woman reading a city map" style="background:linear-gradient(90deg,#c9a27a,#5a86b8)"></div><h4>Lorem ipsum dolor sit</h4><p>Aenean commodo ligula eget dolor. Aenean massa. Cum sociis natoque penatibus et magnis dis parturient adipiscing elit.</p><a>View More...</a></div>
<div class="abs card" style="left:355px;top:548px"><div class="ph" role="img" aria-label="Photographer on a rocky coast" style="background:linear-gradient(180deg,#cfd2cf,#7a7568)"></div><h4>Lorem ipsum dolor sit</h4><p>Aenean commodo ligula eget dolor. Aenean massa. Cum sociis natoque penatibus et magnis dis parturient adipiscing elit.</p><a>View More...</a></div>

<div class="abs bar" style="top:734px">Business Articles<small>View More...</small></div>
<div class="abs card" style="left:94px;top:775px"><div class="ph" role="img" aria-label="Business traveller walking with luggage" style="background:linear-gradient(180deg,#c8c8c4,#e8e6e0)"></div><h4>Lorem ipsum dolor sit</h4><p>Aenean commodo ligula eget dolor. Aenean massa. Cum sociis natoque penatibus et magnis dis parturient adipiscing elit.</p><a>View More...</a></div>
<div class="abs card" style="left:225px;top:775px"><div class="ph" role="img" aria-label="Businessman waiting in an airport lounge" style="background:linear-gradient(180deg,#d8dcde,#3b4652)"></div><h4>Lorem ipsum dolor sit</h4><p>Aenean commodo ligula eget dolor. Aenean massa. Cum sociis natoque penatibus et magnis dis parturient adipiscing elit.</p><a>View More...</a></div>
<div class="abs card" style="left:355px;top:775px"><div class="ph" role="img" aria-label="Business people working at an airport" style="background:linear-gradient(180deg,#a9b2b8,#4a4e52)"></div><h4>Lorem ipsum dolor sit</h4><p>Aenean commodo ligula eget dolor. Aenean massa. Cum sociis natoque penatibus et magnis dis parturient adipiscing elit.</p><a>View More...</a></div>

<h2 class="sec" style="top:964px">Ethos of Breakfree418</h2>
<div class="abs ethos">
  <div class="video" role="img" aria-label="Video player showing an aerial view of an island in the ocean"></div>
  <h3>Aenean commodo ligula</h3>
  <p>Aenean massa. Cum sociis natoque penatibus et magnis dis parturient montes, nascetur ridiculus mus. Donec quam felis, ultricies nec, pellentesque eu, pretium quis, sem. Nulla consequat massa quis enim. Donec pede justo, fringilla vel, aliquet nec, vulputate eget, arcu. In enim justo, rhoncus ut, imperdiet a, venenatis vitae,Lorem ipsum dolor sit amet, consectetuer adipiscing elit. Nulla consequat massa quis enim. Donec pede justo. Lorem ipsum dolor sit amet, consectetuer adipiscing elit.</p>
</div>

<div class="abs side" style="top:318px;height:232px;padding-top:42px">
  <div class="bucket"><div class="th" role="img" aria-label="Harbour bridge and city skyline" style="background:linear-gradient(180deg,#b7cde0,#5d7a94)"></div><div><b>This is a sample Post 1</b><p>Lorem ipsum dolor sit amet, consectetuer adipiscing elit, sed diam nonummy nibh...</p></div></div>
  <div class="bucket"><div class="th" role="img" aria-label="Tropical beach with a boat" style="background:linear-gradient(180deg,#3a8fd0,#2fb0b8 60%,#e0d3a8)"></div><div><b>This is a sample Post 1</b><p>Lorem ipsum dolor sit amet, consectetuer adipiscing elit, sed diam nonummy nibh...</p></div></div>
  <div class="bucket" style="border:0"><div class="th" role="img" aria-label="Couple relaxing on beach chairs" style="background:linear-gradient(180deg,#5aa6de,#d9c7a0)"></div><div><b>This is a sample Post 1</b><p>Lorem ipsum dolor sit amet, consectetuer adipiscing elit, sed diam nonummy nibh...</p></div></div>
</div>
<div class="abs shead" style="top:318px">My bucket list</div>

<div class="abs side" style="top:559px;height:214px;padding-top:44px">
  <div class="news">Lorem ipsum dolor sit amet, conseczvxhcvetuer adipiscing elit, sed diam nonummbmbby nibh<a>http://lnk.example/trg87z</a><em>24 minutes ago</em></div>
  <div class="news">Lorem ipsum dolor sit amet, consevbnvbctetuer adipiscing elit, sed diam nonumbmbmy nibh<a>http://lnk.example/trg87z</a><em>24 minutes ago</em></div>
  <div class="news">Lorem ipsum dolor sit amet, consevnvgjkctetuer adipiscing elit, sed diam nonumvnvjfgmy nibh<a>http://lnk.example/trg87z</a><em>24 minutes ago</em></div>
</div>
<div class="abs shead" style="top:559px">Top Articles</div>

<div class="abs side" style="top:783px;height:214px;padding-top:44px">
  <div class="news">Lorem ipsum dolor sit amet, conseczvxhcvetuer adipiscing elit, sed diam nonummbmbby nibh<a>http://lnk.example/trg87z</a><em>24 minutes ago</em></div>
  <div class="news">Lorem ipsum dolor sit amet, consevbnvbctetuer adipiscing elit, sed diam nonumbmbmy nibh<a>http://lnk.example/trg87z</a><em>24 minutes ago</em></div>
  <div class="news">Lorem ipsum dolor sit amet, consevnvgjkctetuer adipiscing elit, sed diam nonumvnvjfgmy nibh<a>http://lnk.example/trg87z</a><em>24 minutes ago</em></div>
</div>
<div class="abs shead" style="top:783px">Latest News</div>

<div class="abs side" style="top:1006px;height:136px"></div>
<div class="abs shead" style="top:1006px">Subscribe for Newsletter</div>
<div class="abs input">Enter Your E-Mail ID</div>
<div class="abs btn" style="left:606px;top:1078px;width:66px;height:22px;font:500 11px 'Ubuntu',sans-serif">Submit</div>
<div class="abs social">Social Media:</div>
<div class="abs icons"><i></i><i></i><i></i><i></i></div>

<footer class="footer">
  <span style="left:92px">Privacy Policy | Terms of Services | Sitemap</span>
  <span style="right:96px">© Copyright 2012 All rights reserved.</span>
</footer>
</body>
</html>
```